One Thumbnail for Online Shop for PowerPoint Templates needed

We are selling PowerPoint Templates and need therefore a thumbnail for our online shop.

You can use a stock photo, mock-ups or other design elements.

Format:
squared like 500 x 500
or wide like 1280 x 720

If you want to use a title, use:

"Graphs" ---> Title
"PowerPoint template" ---> subtitle

Attachments:
- OLD: Our old thumbnail which I do not like
- Template: PowerPoint pictures which you can use ( you can also copy them if you need more than these)
- Example: Some examples I found from other shops (please do not copy them exactly, only to show what I mean)

I received lots of designs until now but many are not what I have expected

Target Market(s)

E-Commerce

Industry/Entity Type

Shop

Font styles to use
Sans Serif

Requirements
Should not have
• Do NOT re-design one of the template.png (these are only examples, I will replace them later)

```html
<!DOCTYPE html>
<html lang="en">
<head>
<meta charset="utf-8">
<title>Standard Graphs – Slide Craft Presentation</title>
<link rel="stylesheet" href="https://fonts.googleapis.com/css2?family=Raleway:wght@300;400&family=Open+Sans:wght@400;700&display=swap">
<style>
  :root {
    --canvas: #f1efec;
    --ink: #333333;
    --muted: #8a8a8a;
    --slide: #ffffff;
    --grid: #d9d9d9;
    --blue: #4a8fdc;
    --navy: #1f3f75;
    --shadow: rgba(0, 0, 0, 0.14);
  }
  * { margin: 0; padding: 0; box-sizing: border-box; }
  html, body { width: 1200px; height: 750px; overflow: hidden; }
  body { background: var(--canvas); font-family: "Open Sans", sans-serif; color: var(--ink); position: relative; }

  .title-block { position: absolute; left: 60px; top: 100px; }
  .title-main { font-family: "Raleway", sans-serif; font-weight: 400; font-size: 96px; line-height: 0.98; letter-spacing: -1px; color: var(--ink); }
  .title-sub { margin-top: 22px; font-family: "Raleway", sans-serif; font-weight: 300; font-size: 50px; line-height: 1.1; letter-spacing: 1px; color: var(--ink); }

  .slide { position: absolute; background: var(--slide); box-shadow: 0 6px 18px var(--shadow); }
  .slide svg { display: block; width: 100%; height: 100%; }
  .slide-feature { left: 545px; top: 60px; width: 610px; height: 345px; }
  .slide-small { top: 510px; width: 340px; height: 200px; }
  .slide-grid { left: 40px; }
  .slide-trend { left: 430px; }
  .slide-ranking { left: 820px; }

  .s-title { font-family: "Open Sans", sans-serif; font-weight: 700; fill: var(--ink); text-anchor: middle; }
  .s-sub { fill: var(--muted); text-anchor: middle; }
  .c-label { font-weight: 700; fill: var(--ink); }
  .c-axis { fill: var(--muted); text-anchor: middle; }
  .bullet { fill: var(--muted); }
  .axis-line { stroke: var(--grid); stroke-width: 1; }
  .line-series { fill: none; stroke: var(--blue); stroke-width: 2; }
  .line-dot { fill: var(--blue); }
  .bar { fill: var(--blue); }
  .bar-dark { fill: var(--navy); }
</style>
</head>
<body>

<div class="title-block">
  <h1 class="title-main">Standard<br>Graphs</h1>
  <p class="title-sub">Slide Craft<br>Presentation 1</p>
</div>

<!-- Feature slide: two line charts, two bar charts -->
<div class="slide slide-feature">
  <svg viewBox="0 0 600 340" font-family="Open Sans, sans-serif">
    <text class="s-title" x="300" y="30" font-size="19">Lorem ipsum dolor sit amet</text>
    <text class="s-sub" x="300" y="46" font-size="7.5">Lorem ipsum dolor sit amet, consectetuer adipiscing elit. Aenean commodo ligula eget dolor</text>

    <text class="c-label" x="20" y="70" font-size="9">Lorem ipsum</text>
    <line class="axis-line" x1="40" y1="78" x2="40" y2="172"/>
    <line class="axis-line" x1="40" y1="172" x2="295" y2="172"/>
    <polyline class="line-series" points="50,148 71,140 92,115 113,100 134,115 155,124 176,130 197,140 218,150 239,160 260,145 281,148"/>
    <g class="line-dot">
      <circle cx="50" cy="148" r="2.5"/><circle cx="71" cy="140" r="2.5"/><circle cx="92" cy="115" r="2.5"/><circle cx="113" cy="100" r="2.5"/><circle cx="134" cy="115" r="2.5"/><circle cx="155" cy="124" r="2.5"/><circle cx="176" cy="130" r="2.5"/><circle cx="197" cy="140" r="2.5"/><circle cx="218" cy="150" r="2.5"/><circle cx="239" cy="160" r="2.5"/><circle cx="260" cy="145" r="2.5"/><circle cx="281" cy="148" r="2.5"/>
    </g>
    <g class="c-axis" font-size="6">
      <text x="50" y="182">Jan</text><text x="71" y="182">Feb</text><text x="92" y="182">Mar</text><text x="113" y="182">Apr</text><text x="134" y="182">May</text><text x="155" y="182">Jun</text><text x="176" y="182">Jul</text><text x="197" y="182">Aug</text><text x="218" y="182">Sep</text><text x="239" y="182">Oct</text><text x="260" y="182">Nov</text><text x="281" y="182">Dec</text>
    </g>

    <text class="c-label" x="320" y="70" font-size="9">Lorem ipsum</text>
    <line class="axis-line" x1="335" y1="78" x2="335" y2="172"/>
    <line class="axis-line" x1="335" y1="172" x2="585" y2="172"/>
    <polyline class="line-series" points="345,160 371,112 397,102 423,130 449,140 475,150 501,144 527,155 553,165 575,158"/>
    <g class="line-dot">
      <circle cx="345" cy="160" r="2.5"/><circle cx="371" cy="112" r="2.5"/><circle cx="397" cy="102" r="2.5"/><circle cx="423" cy="130" r="2.5"/><circle cx="449" cy="140" r="2.5"/><circle cx="475" cy="150" r="2.5"/><circle cx="501" cy="144" r="2.5"/><circle cx="527" cy="155" r="2.5"/><circle cx="553" cy="165" r="2.5"/><circle cx="575" cy="158" r="2.5"/>
    </g>
    <g class="c-axis" font-size="6">
      <text x="345" y="182">Jan</text><text x="371" y="182">Feb</text><text x="397" y="182">Mar</text><text x="423" y="182">Apr</text><text x="449" y="182">May</text><text x="475" y="182">Jun</text><text x="501" y="182">Jul</text><text x="527" y="182">Aug</text><text x="553" y="182">Sep</text><text x="575" y="182">Oct</text>
    </g>

    <text class="c-label" x="20" y="206" font-size="9">Lorem ipsum</text>
    <line class="axis-line" x1="40" y1="214" x2="40" y2="310"/>
    <line class="axis-line" x1="40" y1="310" x2="295" y2="310"/>
    <g class="bar">
      <rect x="44" y="240" width="14" height="70"/><rect x="66" y="242" width="14" height="68"/><rect x="89" y="230" width="14" height="80"/><rect x="112" y="245" width="14" height="65"/><rect x="134" y="255" width="14" height="55"/><rect x="157" y="260" width="14" height="50"/><rect x="180" y="245" width="14" height="65"/><rect x="203" y="250" width="14" height="60"/><rect x="226" y="256" width="14" height="54"/><rect x="248" y="250" width="14" height="60"/><rect x="271" y="266" width="14" height="44"/>
    </g>
    <g class="c-axis" font-size="6">
      <text x="51" y="320">Jan</text><text x="73" y="320">Feb</text><text x="96" y="320">Mar</text><text x="119" y="320">Apr</text><text x="141" y="320">May</text><text x="164" y="320">Jun</text><text x="187" y="320">Jul</text><text x="210" y="320">Aug</text><text x="233" y="320">Sep</text><text x="255" y="320">Oct</text><text x="278" y="320">Nov</text>
    </g>

    <text class="c-label" x="320" y="226" font-size="9">Lorem ipsum</text>
    <line class="axis-line" x1="335" y1="234" x2="335" y2="310"/>
    <line class="axis-line" x1="335" y1="310" x2="585" y2="310"/>
    <g class="bar">
      <rect x="340" y="258" width="16" height="52"/><rect x="364" y="254" width="16" height="56"/><rect x="388" y="262" width="16" height="48"/><rect x="412" y="246" width="16" height="64"/><rect x="436" y="266" width="16" height="44"/><rect x="460" y="262" width="16" height="48"/><rect x="484" y="272" width="16" height="38"/><rect x="508" y="262" width="16" height="48"/><rect x="532" y="276" width="16" height="34"/><rect x="556" y="266" width="16" height="44"/>
    </g>
    <g class="c-axis" font-size="6">
      <text x="348" y="320">Jan</text><text x="372" y="320">Feb</text><text x="396" y="320">Mar</text><text x="420" y="320">Apr</text><text x="444" y="320">May</text><text x="468" y="320">Jun</text><text x="492" y="320">Jul</text><text x="516" y="320">Aug</text><text x="540" y="320">Sep</text><text x="564" y="320">Oct</text>
    </g>
  </svg>
</div>

<!-- Small slide: four bar charts with notes -->
<div class="slide slide-small slide-grid">
  <svg viewBox="0 0 340 200" font-family="Open Sans, sans-serif">
    <defs>
      <g id="mini-bars">
        <line class="axis-line" x1="8" y1="4" x2="8" y2="62"/>
        <line class="axis-line" x1="8" y1="62" x2="96" y2="62"/>
        <rect class="bar" x="12" y="30" width="5" height="32"/><rect class="bar-dark" x="18" y="26" width="5" height="36"/>
        <rect class="bar" x="28" y="32" width="5" height="30"/><rect class="bar-dark" x="34" y="30" width="5" height="32"/>
        <rect class="bar" x="44" y="36" width="5" height="26"/><rect class="bar-dark" x="50" y="34" width="5" height="28"/>
        <rect class="bar" x="60" y="38" width="5" height="24"/><rect class="bar-dark" x="66" y="36" width="5" height="26"/>
        <rect class="bar" x="76" y="40" width="5" height="22"/><rect class="bar-dark" x="82" y="42" width="5" height="20"/>
      </g>
    </defs>
    <text class="s-title" x="170" y="18" font-size="11">Lorem ipsum dolor sit amet</text>
    <text class="s-sub" x="170" y="28" font-size="4.5">Lorem ipsum dolor sit amet, consectetuer adipiscing elit. Aenean commodo ligula eget dolor</text>
    <text class="c-label" x="15" y="42" font-size="5">Lorem ipsum</text>
    <text class="c-label" x="120" y="42" font-size="5">Lorem ipsum</text>
    <text class="c-label" x="15" y="120" font-size="5">Lorem ipsum</text>
    <text class="c-label" x="120" y="120" font-size="5">Lorem ipsum</text>
    <use href="#mini-bars" x="12" y="44"/>
    <use href="#mini-bars" x="117" y="44"/>
    <use href="#mini-bars" x="12" y="122"/>
    <use href="#mini-bars" x="117" y="122"/>
    <g class="bullet" font-size="4.5">
      <text x="226" y="60">• Lorem ipsum dolor sit amet</text><text x="230" y="67">consectetuer adipiscing elit</text>
      <text x="226" y="100">• Aenean commodo ligula eget</text><text x="230" y="107">dolor massa cum sociis</text>
      <text x="226" y="140">• Natoque penatibus et magnis</text><text x="230" y="147">dis parturient montes nascetur</text>
    </g>
  </svg>
</div>

<!-- Small slide: rising bar chart with trend line -->
<div class="slide slide-small slide-trend">
  <svg viewBox="0 0 340 200" font-family="Open Sans, sans-serif">
    <text class="s-title" x="170" y="18" font-size="11">Lorem ipsum dolor sit amet</text>
    <text class="s-sub" x="170" y="28" font-size="4.5">Lorem ipsum dolor sit amet, consectetuer adipiscing elit. Aenean commodo ligula eget dolor</text>
    <g class="bullet" font-size="4.5">
      <text x="15" y="65">• Donec quam felis ultricies</text><text x="19" y="72">nec pellentesque eu pretium</text>
      <text x="15" y="110">• Nulla consequat massa quis</text><text x="19" y="117">enim donec pede justo</text>
    </g>
    <line class="axis-line" x1="128" y1="45" x2="128" y2="180"/>
    <line class="axis-line" x1="128" y1="180" x2="330" y2="180"/>
    <g class="bar">
      <rect x="133" y="150" width="9" height="30"/><rect x="147" y="143" width="9" height="37"/><rect x="161" y="138" width="9" height="42"/><rect x="175" y="130" width="9" height="50"/><rect x="189" y="122" width="9" height="58"/><rect x="203" y="115" width="9" height="65"/><rect x="217" y="108" width="9" height="72"/><rect x="231" y="100" width="9" height="80"/><rect x="245" y="94" width="9" height="86"/><rect x="259" y="88" width="9" height="92"/><rect x="273" y="82" width="9" height="98"/><rect x="287" y="78" width="9" height="102"/><rect x="301" y="74" width="9" height="106"/><rect x="315" y="70" width="9" height="110"/>
    </g>
    <polyline class="line-series" stroke-width="1" points="137,140 151,128 165,120 179,108 193,98 207,88 221,76 235,68 249,62 263,58 277,56 291,54 305,52 319,52"/>
  </svg>
</div>

<!-- Small slide: horizontal ranking bars -->
<div class="slide slide-small slide-ranking">
  <svg viewBox="0 0 340 200" font-family="Open Sans, sans-serif">
    <text class="s-title" x="170" y="18" font-size="11">Lorem ipsum dolor sit amet</text>
    <text class="s-sub" x="170" y="28" font-size="4.5">Lorem ipsum dolor sit amet, consectetuer adipiscing elit. Aenean commodo ligula eget dolor</text>
    <text class="c-label" x="15" y="42" font-size="5">Lorem ipsum</text>
    <line class="axis-line" x1="30" y1="46" x2="30" y2="182"/>
    <g class="bar-dark">
      <rect x="30" y="50" width="140" height="7"/><rect x="30" y="61" width="136" height="7"/><rect x="30" y="72" width="132" height="7"/><rect x="30" y="83" width="128" height="7"/><rect x="30" y="94" width="124" height="7"/><rect x="30" y="105" width="120" height="7"/><rect x="30" y="116" width="116" height="7"/><rect x="30" y="127" width="112" height="7"/><rect x="30" y="138" width="108" height="7"/><rect x="30" y="149" width="104" height="7"/><rect x="30" y="160" width="100" height="7"/><rect x="30" y="171" width="96" height="7"/>
    </g>
    <line class="axis-line" x1="200" y1="46" x2="200" y2="182"/>
    <g class="bar">
      <rect x="200" y="50" width="22" height="7"/><rect x="200" y="61" width="30" height="7"/><rect x="200" y="72" width="14" height="7"/><rect x="200" y="83" width="26" height="7"/><rect x="200" y="94" width="18" height="7"/><rect x="200" y="105" width="34" height="7"/><rect x="200" y="116" width="10" height="7"/><rect x="200" y="127" width="20" height="7"/><rect x="200" y="138" width="28" height="7"/><rect x="200" y="149" width="16" height="7"/><rect x="200" y="160" width="24" height="7"/><rect x="200" y="171" width="12" height="7"/>
    </g>
  </svg>
</div>

</body>
</html>
```